UI Improvement for FlorKeep app

We are looking for a talented UI/UX designer to REFINE and enhance the visual design of our mobile application, FlorKeep. The app is fully functional, but we need a designer to improve its aesthetics by specifying design elements such as fonts, colors, spacing, and component styles.
Your task will be to analyze the CURRENT UI and provide detailed design specifications that will make the app more visually appealing, modern, and user-friendly.
TODO:
Review the existing FlorKeep app design (see attachments) and identify areas for visual improvement.
Provide a detailed UI style guide, including:
Typography (font choices, sizes, and weights)
Color palette (primary, secondary, and accent colors)
Component styling (buttons, forms, icons, and interactive elements)
Spacing and layout guidelines (margins, paddings, and alignment)
Ensure the design remains clean, modern, and professional while maintaining usability and accessibility.
Provide design mockups or visual examples (if possible) to illustrate the proposed changes.
Deliverables:
A UI Style Guide (PDF or Drafta file) with specifications on fonts, colors, spacing, and UI components.
Optionally, before/after mockups or examples demonstrating the improvements.
Ideal Designer:
Strong experience in mobile UI/UX design.
Understanding of modern design trends and best practices.
Ability to communicate design choices clearly for easy developer implementation.
I have attached 7 images showcasing the main UI screens used in the FlorKeep app. These screens need visual enhancements to improve their overall look and user experience.
The images represent the current design in three key modes:
LIST Mode – Displays data in a structured list format.
READ Mode – Shows detailed information when a user selects an item.
ADD/EDIT Mode – Allows users to input or modify information.
Additionally, there is a ‘MORE’ page, which serves as a menu listing other features of the application.
Task Objective:
Please refine and improve these UIs to create a more modern, visually appealing, and user-friendly experience. Focus on typography, colors, spacing, and component styling to ensure a cohesive and polished design.
Look and feel
Each slider illustrates characteristics of the customer's brand and the style your logo design should communicate.

```html
<!DOCTYPE html>
<html lang="en">
<head>
<meta charset="utf-8">
<title>UI Improvement for FlorKeep App</title>
<link href="https://fonts.googleapis.com/css2?family=Inter:wght@400;500;600;700;800&display=swap" rel="stylesheet">
<style>
:root{
  --blue:#1f5bb5;
  --blue-2:#2a68c9;
  --ink:#1d2230;
  --muted:#9aa1ad;
  --line:#e4e7ee;
  --page:#eff0f2;
  --page-top:#e4e5e8;
  --screen:#f4f6fa;
  --green:#1c9b4b;
  --green-bg:#e3f6e9;
  --sky:#e6f0fd;
  --link:#1b6fe0;
  --old-blue:#1414c8;
  --faint:#e2e3e6;
}
*{box-sizing:border-box;margin:0;padding:0}
html,body{width:1200px;height:2193px;overflow:hidden}
body{background:var(--page);font-family:"Inter",sans-serif;color:var(--ink)}
.board{position:absolute;left:0;top:0;width:1409px;height:2576px;transform:scale(.85167);transform-origin:0 0;background:linear-gradient(180deg,var(--page-top) 0,var(--page-top) 880px,var(--page) 880px)}
.abs{position:absolute}

/* headline */
.headline{position:absolute;top:84px;left:0;width:1409px;text-align:center;font-size:40px;font-weight:800;letter-spacing:.2px;color:#1c1d20}
.spec-k{position:absolute;top:180px;font-size:16px;font-weight:500;letter-spacing:.5px;color:#1c1d20}
.spec-v{position:absolute;top:208px;font-size:22px;font-weight:500;color:#1c1d20}
.tool{position:absolute;left:742px;top:208px;width:36px;height:36px;border-radius:7px;background:#fff;display:grid;place-items:center;font-size:7px;font-weight:600;color:#1c1d20}

/* section labels */
.label{position:absolute;font-size:12.5px;font-weight:600;color:#2a2b2f;letter-spacing:.2px;white-space:nowrap}
.label.small{font-size:8.5px}
.connector{position:absolute;background:#9aa0a8}

/* screens */
.screen{position:absolute;width:233px;background:var(--screen);border-radius:26px;overflow:hidden;border:1px solid #d3d7de;box-shadow:0 6px 18px rgba(20,30,50,.12);transform-origin:0 0}
.hdr{position:absolute;left:0;top:0;right:0;height:115px;background:linear-gradient(160deg,#1a4fa3 0%,#2462c2 55%,#1d58b3 100%)}
.status{position:absolute;top:12px;left:14px;right:14px;display:flex;justify-content:space-between;align-items:center;color:#fff;font-size:8px}
.status .sig{display:flex;gap:3px;align-items:center}
.status .sig i{display:block;width:9px;height:6px;background:#fff;border-radius:1px;opacity:.9}
.topbar{position:absolute;top:42px;left:12px;right:12px;height:16px;display:flex;align-items:center;gap:5px}
.circ{width:13px;height:13px;border-radius:50%;background:rgba(255,255,255,.28);display:grid;place-items:center;flex:none}
.circ svg{width:8px;height:8px;color:#fff}
.title{flex:1;text-align:center;color:#fff;font-size:13px;font-weight:600}
.pbtn{background:rgba(255,255,255,.28);color:#fff;font-size:7.5px;font-weight:500;padding:3px 10px;border-radius:10px}

.body{position:absolute;top:73px;left:10px;right:10px}
.card{background:#fff;border-radius:8px;padding:12px 10px 10px}
.ch{display:flex;justify-content:space-between;align-items:center;font-size:10.5px;font-weight:500;color:#2a2f3a;padding:0 2px}
.ch .dots{color:#c3c8d1;font-size:10px;letter-spacing:1px}
.ch svg{width:9px;height:9px;color:var(--blue)}
.ch.sub{margin-top:16px;padding:0 6px}

.f{display:flex;align-items:center;height:36px;border:1px solid var(--line);border-radius:5px;padding:0 10px;margin-top:8px;background:#fff}
.ic{width:16px;height:16px;display:grid;place-items:center;margin-right:12px;flex:none;color:#a3a9b4}
.ic svg{width:13px;height:13px}
.tinted .ic{width:18px;height:18px;border-radius:50%;background:var(--sky);color:var(--blue)}
.tinted .ic svg{width:10px;height:10px}
.fx{flex:1;min-width:0}
.lbl{display:block;font-size:6.5px;color:#adb3be}
.lbl b{color:var(--blue);font-weight:700}
.val{display:block;font-size:8.5px;color:var(--ink);margin-top:3px;white-space:nowrap}
.f .dd{width:8px;height:8px;color:#4a5060}
.pair{display:flex;gap:8px}
.pair .f{flex:1}

/* lists */
.search{height:28px;background:#fff;border:1px solid var(--line);border-radius:6px;display:flex;align-items:center;padding:0 8px;font-size:8.5px;color:#3a3f4a;gap:8px}
.search .s{width:10px;height:10px;color:#9aa1ad}
.search .sp{flex:1}
.filter{width:15px;height:15px;border-radius:50%;background:var(--link);display:grid;place-items:center}
.filter svg{width:8px;height:8px;color:#fff}
.chip{display:flex;align-items:center;gap:6px;padding:4px 6px;border-right:1px solid var(--line);font-size:8px;color:#3a3f4a}
.chip svg{width:7px;height:7px;color:#3a3f4a}
.sec{display:flex;justify-content:space-between;align-items:center;font-size:10px;color:#333;padding:12px 4px 8px}
.sec svg{width:8px;height:8px;color:#7d8490}
.item{display:flex;align-items:center;background:#fff;border-radius:6px;padding:9px 9px;margin-bottom:8px;gap:10px}
.avatar{width:32px;height:32px;border-radius:50%;background:radial-gradient(circle at 50% 38%,#8ea2c0 0,#4d5f7e 45%,#1f2a3e 100%);flex:none}
.meta{flex:1;min-width:0}
.nm{font-size:9px;color:var(--ink);white-space:nowrap}
.tags{display:flex;gap:5px;margin-top:6px;align-items:center}
.tag{font-size:6.5px;padding:2px 6px;border-radius:8px;white-space:nowrap}
.tag.ao{color:var(--green);padding-left:1px;padding-right:1px}
.tag.en{background:var(--sky);color:var(--link)}
.tag.qp{background:var(--green-bg);color:var(--green)}
.tag.pi{background:#eef0f3;color:#555b66}
.tag.num{background:var(--sky);color:var(--link);font-weight:500}
.date{margin-left:auto;font-size:7px;color:#b0b6c0}

/* tab bar */
.tabbar{position:absolute;left:0;right:0;bottom:0;height:50px;background:#fff;display:flex;align-items:center;justify-content:space-between;padding:0 18px 6px}
.tabbar svg{width:13px;height:13px;color:#b7c0cf}
.tab-on{background:var(--blue);color:#fff;border-radius:12px;padding:5px 10px;font-size:7.5px;font-weight:500;display:flex;gap:5px;align-items:center}
.tab-on svg{width:9px;height:9px;color:#fff}

/* legacy screens */
.old{position:absolute;background:#fff;overflow:hidden;border:1px solid #dcdde0}
.old .sb{background:#000;color:#fff;height:24px;font-size:8.5px;display:flex;align-items:center;justify-content:space-between;padding:0 22px}
.old .nav{display:flex;align-items:center;justify-content:space-between;padding:6px 10px;font-size:9px;color:#444}
.old .nav .c{text-align:center;flex:1}
.old .osearch{margin:2px 3px 4px;border:1px solid #c8c9cc;height:18px;display:flex;align-items:center;justify-content:space-between;padding:0 6px;font-size:7px;color:#666}
.old .osearch em{font-style:normal;font-size:5px;color:#89a6c9;text-align:right;line-height:1}
.orow{display:flex;align-items:center;gap:7px;border:1px solid #c9cace;margin:0 3px 3px;padding:4px 6px;min-height:40px}
.lt{width:26px;height:28px;border:1px solid #8c97b5;color:#8a8f9a;display:grid;place-items:center;font-size:12px;flex:none}
.on{color:var(--old-blue);font-weight:700;font-size:7.5px}
.otags{display:flex;gap:8px;margin-top:6px;font-size:5.3px;font-weight:700;color:#222}
.otags .q{background:#7fe08a;padding:0 3px}
.otab{position:absolute;left:0;right:0;bottom:8px;display:flex;justify-content:space-around;font-size:5.5px;color:#222;text-align:center}
.otab span{display:flex;flex-direction:column;align-items:center;gap:2px}
.otab i{display:block;width:6px;height:6px;background:#222;border-radius:50%}
.otab .on2{color:#3a7bd5}
.otab .on2 i{background:#3a7bd5}
.ofl{margin:5px 6px 0;border:1px solid #8da4d4;border-radius:2px;padding:2px 5px 5px;position:relative}
.ofl .ol{font-size:4.5px;color:#2040c0;font-weight:600}
.ofl .oi{margin-top:2px;border:1px solid #4a74d6;height:14px;font-size:5px;color:#999;padding:3px 4px}
.ofl .od{position:absolute;right:-12px;top:14px;font-size:8px;color:#333}
.homebar{position:absolute;bottom:2px;left:50%;width:60px;height:2px;margin-left:-30px;background:#333;border-radius:2px}

.footnote{position:absolute;top:2372px;left:0;width:1409px;text-align:center;font-size:15.5px;font-weight:500;color:#1c1d20}
.thanks{position:absolute;top:2432px;left:0;width:1409px;text-align:center;font-size:38px;font-weight:800;color:var(--faint)}
</style>
</head>
<body>
<svg width="0" height="0" style="position:absolute" aria-hidden="true">
  <defs>
    <symbol id="i-user" viewBox="0 0 16 16"><circle cx="8" cy="5" r="3" fill="none" stroke="currentColor" stroke-width="1.3"/><path d="M2.5 14c.6-3 2.8-4.5 5.5-4.5s4.9 1.5 5.5 4.5" fill="none" stroke="currentColor" stroke-width="1.3"/></symbol>
    <symbol id="i-brief" viewBox="0 0 16 16"><rect x="1.5" y="4.5" width="13" height="9" rx="1.5" fill="none" stroke="currentColor" stroke-width="1.3"/><path d="M5.5 4.5V3h5v1.5M1.5 8.5h13" fill="none" stroke="currentColor" stroke-width="1.3"/></symbol>
    <symbol id="i-pin" viewBox="0 0 16 16"><path d="M8 14.5s5-4.6 5-8.2A5 5 0 0 0 3 6.3c0 3.6 5 8.2 5 8.2z" fill="none" stroke="currentColor" stroke-width="1.3"/><circle cx="8" cy="6.3" r="1.8" fill="none" stroke="currentColor" stroke-width="1.3"/></symbol>
    <symbol id="i-bldg" viewBox="0 0 16 16"><path d="M2 14.5V4l6-2.5v13M8 6.5h6v8M1 14.5h14M4 6h2M4 9h2M4 12h2M10 9h2M10 12h2" fill="none" stroke="currentColor" stroke-width="1.2"/></symbol>
    <symbol id="i-search" viewBox="0 0 16 16"><circle cx="7" cy="7" r="4.8" fill="none" stroke="currentColor" stroke-width="1.5"/><path d="M10.5 10.5L14 14" stroke="currentColor" stroke-width="1.5"/></symbol>
    <symbol id="i-chev" viewBox="0 0 16 16"><path d="M3.5 6l4.5 4.5L12.5 6" fill="none" stroke="currentColor" stroke-width="2"/></symbol>
    <symbol id="i-back" viewBox="0 0 16 16"><path d="M10 3L5 8l5 5" fill="none" stroke="currentColor" stroke-width="2.2"/></symbol>
    <symbol id="i-dots" viewBox="0 0 16 16"><circle cx="3.5" cy="8" r="1.4" fill="currentColor"/><circle cx="8" cy="8" r="1.4" fill="currentColor"/><circle cx="12.5" cy="8" r="1.4" fill="currentColor"/></symbol>
    <symbol id="i-filter" viewBox="0 0 16 16"><path d="M2 3h12l-4.7 5.5V13L6.7 14V8.5z" fill="none" stroke="currentColor" stroke-width="1.6"/></symbol>
    <symbol id="i-chat" viewBox="0 0 16 16"><path d="M8 1.5a6 6 0 0 0-6 6c0 1.9.9 3.5 2.2 4.6L4 15l3-1.6A6 6 0 1 0 8 1.5z" fill="currentColor"/></symbol>
    <symbol id="i-case" viewBox="0 0 16 16"><rect x="1.5" y="4.5" width="13" height="9.5" rx="1.5" fill="currentColor"/><path d="M5.5 4.5V2.5h5v2" fill="none" stroke="currentColor" stroke-width="1.4"/></symbol>
    <symbol id="i-doc" viewBox="0 0 16 16"><rect x="3" y="1.5" width="10" height="13" rx="1.5" fill="currentColor"/><path d="M5.5 5.5h5M5.5 8h5M5.5 10.5h3" stroke="#fff" stroke-width="1.1"/></symbol>
    <symbol id="i-grid" viewBox="0 0 16 16"><rect x="1.5" y="1.5" width="5.5" height="5.5" rx="1.6" fill="currentColor"/><rect x="9" y="1.5" width="5.5" height="5.5" rx="1.6" fill="currentColor"/><rect x="1.5" y="9" width="5.5" height="5.5" rx="1.6" fill="currentColor"/><rect x="9" y="9" width="5.5" height="5.5" rx="1.6" fill="currentColor"/></symbol>
    <symbol id="i-card" viewBox="0 0 16 16"><rect x="2" y="1.5" width="12" height="13" rx="2" fill="currentColor"/><circle cx="8" cy="6.3" r="2" fill="#1f5bb5"/><path d="M4.8 12c.5-1.8 1.7-2.7 3.2-2.7s2.7.9 3.2 2.7" fill="#1f5bb5"/></symbol>
    <symbol id="i-pilot" viewBox="0 0 16 16"><circle cx="8" cy="8" r="6.5" fill="currentColor"/><circle cx="8" cy="6.5" r="2" fill="#1f5bb5"/><path d="M4.8 12.2c.6-2 1.7-2.9 3.2-2.9s2.6.9 3.2 2.9" fill="#1f5bb5"/></symbol>
  </defs>
</svg>

<main class="board">

  <h1 class="headline">UI IMPROVEMENT FOR FLORKEEP APP</h1>
  <div class="spec-k" style="left:614px">FONTS</div>
  <div class="spec-k" style="left:739px">TOOLS</div>
  <div class="spec-v" style="left:614px">INTER</div>
  <div class="tool">Drafta</div>

  <!-- ===== Showcase: left Add Contact ===== -->
  <section class="screen" style="left:232px;top:370px;height:494px;transform:scale(.86)">
    <div class="hdr" role="img" aria-label="Header photo of pilots beside an aircraft, tinted blue"></div>
    <div class="status"><span>12:30PM</span><span class="sig"><i></i><i></i></span></div>
    <div class="topbar"><span class="circ"><svg><use href="#i-back"/></svg></span><span class="title">Add Contact</span><span class="pbtn">Save</span><span class="circ"><svg><use href="#i-dots"/></svg></span></div>
    <div class="body"><div class="card">
      <div class="ch">Contact Information <span class="dots">···</span></div>
      <div class="f"><span class="ic"><svg><use href="#i-brief"/></svg></span><div class="fx"><span class="lbl">Business Name -e</span><span class="val">Contact Business name</span></div></div>
      <div class="f"><span class="ic"><svg><use href="#i-user"/></svg></span><div class="fx"><span class="lbl">First Name -e</span><span class="val">Michael</span></div></div>
      <div class="f"><span class="ic"><svg><use href="#i-user"/></svg></span><div class="fx"><span class="lbl">Middle Name -e</span><span class="val">Patrick</span></div></div>
      <div class="f"><span class="ic"><svg><use href="#i-user"/></svg></span><div class="fx"><span class="lbl">Last Name -e</span><span class="val">Johnson</span></div></div>
      <div class="ch sub">Address Information <svg><use href="#i-chev"/></svg></div>
      <div class="f"><span class="ic"><svg><use href="#i-pin"/></svg></span><div class="fx"><span class="lbl">Address Label Tag -e</span><span class="val">Address</span></div></div>
      <div class="f"><span class="ic"><svg><use href="#i-pin"/></svg></span><div class="fx"><span class="lbl">Address Line1 -e <b>*</b></span><span class="val">Michael</span></div></div>
      <div class="f"><span class="ic"><svg><use href="#i-pin"/></svg></span><div class="fx"><span class="lbl">Address Line2 -e <b>*</b></span><span class="val">Patrick</span></div></div>
      <div class="f"><span class="ic"><svg><use href="#i-bldg"/></svg></span><div class="fx"><span class="lbl">Address City</span><span class="val">New York City, NY</span></div></div>
    </div></div>
  </section>

  <!-- ===== Showcase: right Contacts ===== -->
  <section class="screen" style="left:976px;top:370px;height:494px;transform:scale(.86)">
    <div class="hdr" role="img" aria-label="Header photo of pilots beside an aircraft, tinted blue"></div>
    <div class="status"><span>12:30PM</span><span class="sig"><i></i><i></i></span></div>
    <div class="topbar"><span class="circ"><svg><use href="#i-back"/></svg></span><span class="title">Contacts</span><span class="pbtn">Add</span><span class="circ"><svg><use href="#i-dots"/></svg></span></div>
    <div class="body">
      <div class="search"><span class="chip">All <svg><use href="#i-chev"/></svg></span><span class="sp">Search</span><svg class="s"><use href="#i-search"/></svg></div>
      <div style="height:8px"></div>
      <div class="item"><div class="avatar" role="img" aria-label="Portrait photo of a pilot"></div><div class="meta"><div class="nm">Allen, Charles Brent</div><div class="tags"><span class="tag ao">Aircraft Owner</span><span class="tag en">Enthusiast -e</span></div></div></div>
      <div class="item"><div class="avatar" role="img" aria-label="Portrait photo of a pilot"></div><div class="meta"><div class="nm">Aallinger, Richard Simone</div><div class="tags"><span class="tag ao">Aircraft Owner</span><span class="tag qp">Qualified Pilot</span><span class="tag pi">Pilot</span></div></div></div>
      <div class="item"><div class="avatar" role="img" aria-label="Portrait photo of a pilot"></div><div class="meta"><div class="nm">Aalvi, Ava, Simone</div><div class="tags"><span class="tag ao">Aircraft Owner</span><span class="tag qp">Qualified Pilot</span></div></div></div>
      <div class="item"><div class="avatar" role="img" aria-label="Portrait photo of a pilot"></div><div class="meta"><div class="nm">Garner, Cody, Yarehet</div><div class="tags"><span class="tag ao">Aircraft Owner</span><span class="tag qp">Qualified Pilot</span><span class="tag pi">Pilot</span></div></div></div>
      <div class="item"><div class="avatar" role="img" aria-label="Portrait photo of a pilot"></div><div class="meta"><div class="nm">Giles, Joseph, Allen</div><div class="tags"><span class="tag ao">Aircraft Owner</span><span class="tag qp">Qualified Pilot</span><span class="tag pi">Pilot</span></div></div></div>
    </div>
  </section>

  <!-- ===== Showcase: Pilots ===== -->
  <section class="screen" style="left:368px;top:340px;height:530px;transform:scale(.91)">
    <div class="hdr" role="img" aria-label="Header photo of pilots beside an aircraft, tinted blue"></div>
    <div class="status"><span>12:30PM</span><span class="sig"><i></i><i></i></span></div>
    <div class="topbar"><span class="circ"><svg><use href="#i-back"/></svg></span><span class="title">Pilots</span><span class="pbtn">Add</span><span class="circ"><svg><use href="#i-dots"/></svg></span></div>
    <div class="body">
      <div class="search"><svg class="s"><use href="#i-search"/></svg><span class="sp">Search</span><span class="filter"><svg><use href="#i-filter"/></svg></span></div>
      <div class="sec">A <svg><use href="#i-chev"/></svg></div>
      <div class="item"><div class="avatar" role="img" aria-label="Portrait photo of a pilot"></div><div class="meta"><div class="nm">Allen, Charles Brent</div><div class="tags"><span class="tag num">3182133</span><span class="date">9/30/24</span></div></div></div>
      <div class="item"><div class="avatar" role="img" aria-label="Photo of a pilot beside an aircraft"></div><div class="meta"><div class="nm">Aallinger, Richard Simone</div><div class="tags"><span class="tag num">4467155</span><span class="date">5/19/24</span></div></div></div>
      <div class="item"><div class="avatar" role="img" aria-label="Portrait photo of a pilot"></div><div class="meta"><div class="nm">Aalvi, Ava, Simone</div><div class="tags"><span class="tag num">4360575</span><span class="date">2/25/25</span></div></div></div>
      <div class="sec">B <svg><use href="#i-chev"/></svg></div>
      <div class="item"><div class="avatar" role="img" aria-label="Photo of a pilot in a cockpit"></div><div class="meta"><div class="nm">Bornfleth, Aaron, Hector</div><div class="tags"><span class="tag num">4360575</span><span class="date">9/30/24</span></div></div></div>
      <div class="item"><div class="avatar" role="img" aria-label="Portrait photo of a pilot"></div><div class="meta"><div class="nm">Ballinger, Richard</div><div class="tags"><span class="tag num">3423819</span><span class="date">2/28/25</span></div></div></div>
      <div class="sec">C <svg><use href="#i-chev"/></svg></div>
    </div>
  </section>

  <!-- ===== Showcase: Contacts ===== -->
  <section class="screen" style="left:800px;top:338px;height:490px">
    <div class="hdr" role="img" aria-label="Header photo of pilots beside an aircraft, tinted blue"></div>
    <div class="status"><span>12:30PM</span><span class="sig"><i></i><i></i></span></div>
    <div class="topbar"><span class="circ"><svg><use href="#i-back"/></svg></span><span class="title">Contacts</span><span class="pbtn">Add</span><span class="circ"><svg><use href="#i-dots"/></svg></span></div>
    <div class="body">
      <div class="search"><span class="chip">All <svg><use href="#i-chev"/></svg></span><span class="sp">Search</span><svg class="s"><use href="#i-search"/></svg></div>
      <div class="sec">&nbsp; <svg><use href="#i-chev"/></svg></div>
      <div class="item"><div class="avatar" role="img" aria-label="Portrait photo of a pilot"></div><div class="meta"><div class="nm">Allen, Charles Brent</div><div class="tags"><span class="tag ao">Aircraft Owner</span><span class="tag en">Enthusiast -e</span></div></div></div>
      <div class="item"><div class="avatar" role="img" aria-label="Portrait photo of a pilot"></div><div class="meta"><div class="nm">Aallinger, Richard Simone</div><div class="tags"><span class="tag ao">Aircraft Owner</span><span class="tag qp">Qualified Pilot</span><span class="tag pi">Pilot</span></div></div></div>
      <div class="item"><div class="avatar" role="img" aria-label="Portrait photo of a pilot"></div><div class="meta"><div class="nm">Aalvi, Ava, Simone</div><div class="tags"><span class="tag ao">Aircraft Owner</span><span class="tag qp">Qualified Pilot</span></div></div></div>
      <div class="sec">&nbsp; <svg><use href="#i-chev"/></svg></div>
      <div class="item"><div class="avatar" role="img" aria-label="Photo of a pilot in a cockpit"></div><div class="meta"><div class="nm">Bornfleth, Aaron, Hector</div><div class="tags"><span class="tag pi">Pilot</span><span class="date">9/30/24</span></div></div></div>
      <div class="item"><div class="avatar" role="img" aria-label="Portrait photo of a pilot"></div><div class="meta"><div class="nm">Ballinger, Richard</div><div class="tags"><span class="tag pi">Pilot</span><span class="date">2/28/25</span></div></div></div>
    </div>
  </section>

  <!-- ===== Showcase: center Add Contact ===== -->
  <section class="screen" style="left:592px;top:298px;height:554px">
    <div class="hdr" role="img" aria-label="Header photo of pilots beside an aircraft, tinted blue"></div>
    <div class="status"><span>12:30PM</span><span class="sig"><i></i><i></i></span></div>
    <div class="topbar"><span class="circ"><svg><use href="#i-back"/></svg></span><span class="title">Add Contact</span><span class="pbtn">Save</span><span class="circ"><svg><use href="#i-dots"/></svg></span></div>
    <div class="body"><div class="card">
      <div class="ch">Contact Information <span class="dots">···</span></div>
      <div class="f"><span class="ic"><svg><use href="#i-brief"/></svg></span><div class="fx"><span class="lbl">Business Name -e</span><span class="val">Contact Business name</span></div></div>
      <div class="f"><span class="ic"><svg><use href="#i-user"/></svg></span><div class="fx"><span class="lbl">First Name -e</span><span class="val">Michael</span></div></div>
      <div class="f"><span class="ic"><svg><use href="#i-user"/></svg></span><div class="fx"><span class="lbl">Middle Name -e</span><span class="val">Patrick</span></div></div>
      <div class="f"><span class="ic"><svg><use href="#i-user"/></svg></span><div class="fx"><span class="lbl">Last Name -e</span><span class="val">Johnson</span></div></div>
      <div class="ch sub">Address Information <svg><use href="#i-chev"/></svg></div>
      <div class="f"><span class="ic"><svg><use href="#i-pin"/></svg></span><div class="fx"><span class="lbl">Address Label Tag -e</span><span class="val">Address</span></div><svg class="dd"><use href="#i-chev"/></svg></div>
      <div class="f"><span class="ic"><svg><use href="#i-pin"/></svg></span><div class="fx"><span class="lbl">Address Line1 -e <b>*</b></span><span class="val">Michael</span></div></div>
      <div class="f"><span class="ic"><svg><use href="#i-pin"/></svg></span><div class="fx"><span class="lbl">Address Line2 -e <b>*</b></span><span class="val">Patrick</span></div></div>
      <div class="f"><span class="ic"><svg><use href="#i-bldg"/></svg></span><div class="fx"><span class="lbl">Address City</span><span class="val">New York City, NY</span></div></div>
      <div class="pair">
        <div class="f"><div class="fx"><span class="lbl">AddressState</span><span class="val">New York</span></div><svg class="dd"><use href="#i-chev"/></svg></div>
        <div class="f"><div class="fx"><span class="lbl">Zip -e</span><span class="val">10021</span></div></div>
      </div>
    </div></div>
  </section>

  <!-- ===== Row 2 labels ===== -->
  <div class="label" style="left:72px;top:943px">ADD CONTACT - BEFORE</div>
  <div class="label" style="left:366px;top:943px">ADD CONTACT - AFTER</div>
  <div class="label" style="left:644px;top:943px">ADD CONTACT - OPTION ONE</div>
  <div class="label" style="left:941px;top:943px">ADD CONTACT - OPTION TWO</div>

  <!-- Add Contact before -->
  <section class="old" style="left:72px;top:987px;width:181px;height:391px">
    <div class="sb"><span>10:37</span><span>▪ ▪</span></div>
    <div class="nav"><span>←</span><span class="c" style="font-size:6px">Add<br>Contact</span><span style="color:#3a7bd5;font-size:7px">Save &nbsp;<b style="color:#222">···</b></span></div>
    <div style="border:1px solid #ccc;margin:0 4px;padding-bottom:10px;padding-right:14px">
      <div class="ofl"><div class="ol">Business Name -e</div><div class="oi">enter contactbusinessname -e</div><span class="od">···</span></div>
      <div class="ofl"><div class="ol">First Name -e</div><div class="oi">enter contactfirstname -e</div></div>
      <div class="ofl"><div class="ol">Middle Name -e</div><div class="oi">enter contactmiddlename -e</div></div>
      <div class="ofl"><div class="ol">Last Name -e</div><div class="oi">enter contactlastname -e</div></div>
    </div>
    <div style="border:1px solid #ccc;margin:6px 4px 0;padding-bottom:8px;padding-right:14px">
      <div class="ofl" style="margin-top:14px"><div class="ol">AddressLabelTag -e</div><div class="oi"></div><span class="od">···</span></div>
      <div class="ofl"><div class="ol">AddressLine1 -e</div><div class="oi">enter addressline1 -e</div></div>
      <div class="ofl"><div class="ol">AddressLine2 -e</div><div class="oi">enter addressline2 -e</div></div>
      <div style="display:flex;gap:3px;margin:6px 6px 0">
        <div class="ofl" style="margin:0;flex:1"><div class="ol">AddressCity</div><div class="oi">enter addr</div></div>
        <div class="ofl" style="margin:0;flex:1"><div class="ol">AddressState</div><div class="oi"></div></div>
        <div class="ofl" style="margin:0;flex:1"><div class="ol">Zip -e</div><div class="oi">enter addr</div></div>
      </div>
    </div>
    <div class="otab"><span class="on2"><i></i>Contact</span><span><i></i>Quote</span><span><i></i>WorkOrder</span><span><i></i>Invoice</span><span><i></i>More</span></div>
    <div class="homebar"></div>
  </section>

  <!-- Add Contact after -->
  <section class="screen" style="left:312px;top:990px;height:605px">
    <div class="hdr" role="img" aria-label="Header photo of pilots beside an aircraft, tinted blue"></div>
    <div class="status"><span>12:30PM</span><span class="sig"><i></i><i></i></span></div>
    <div class="topbar"><span class="circ"><svg><use href="#i-back"/></svg></span><span class="title">Add Contact</span><span class="pbtn">Save</span><span class="circ"><svg><use href="#i-dots"/></svg></span></div>
    <div class="body"><div class="card">
      <div class="ch">Contact Information <span class="dots">···</span></div>
      <div class="f"><span class="ic"><svg><use href="#i-brief"/></svg></span><div class="fx"><span class="lbl">Business Name -e</span><span class="val">Contact Business name</span></div></div>
      <div class="f"><span class="ic"><svg><use href="#i-user"/></svg></span><div class="fx"><span class="lbl">First Name -e</span><span class="val">Michael</span></div></div>
      <div class="f"><span class="ic"><svg><use href="#i-user"/></svg></span><div class="fx"><span class="lbl">Middle Name -e</span><span class="val">Patrick</span></div></div>
      <div class="f"><span class="ic"><svg><use href="#i-user"/></svg></span><div class="fx"><span class="lbl">Last Name -e</span><span class="val">Johnson</span></div></div>
      <div class="ch sub">Address Information <svg><use href="#i-chev"/></svg></div>
      <div class="f"><span class="ic"><svg><use href="#i-pin"/></svg></span><div class="fx"><span class="lbl">Address Label Tag -e</span><span class="val">Address</span></div><svg class="dd"><use href="#i-chev"/></svg></div>
      <div class="f"><span class="ic"><svg><use href="#i-pin"/></svg></span><div class="fx"><span class="lbl">Address Line1 -e <b>*</b></span><span class="val">Michael</span></div></div>
      <div class="f"><span class="ic"><svg><use href="#i-pin"/></svg></span><div class="fx"><span class="lbl">Address Line2 -e <b>*</b></span><span class="val">Patrick</span></div></div>
      <div class="f"><span class="ic"><svg><use href="#i-bldg"/></svg></span><div class="fx"><span class="lbl">Address City</span><span class="val">New York City, NY</span></div></div>
      <div class="pair">
        <div class="f"><div class="fx"><span class="lbl">AddressState</span><span class="val">New York</span></div><svg class="dd"><use href="#i-chev"/></svg></div>
        <div class="f"><div class="fx"><span class="lbl">Zip -e</span><span class="val">10021</span></div></div>
      </div>
    </div></div>
    <nav class="tabbar"><span class="tab-on"><svg><use href="#i-card"/></svg>Contact</span><svg><use href="#i-chat"/></svg><svg><use href="#i-case"/></svg><svg><use href="#i-doc"/></svg><svg><use href="#i-grid"/></svg></nav>
  </section>

  <!-- Add Contact option one -->
  <section class="screen tinted" style="left:622px;top:990px;height:610px">
    <div class="hdr" role="img" aria-label="Header photo of pilots beside an aircraft, tinted blue"></div>
    <div class="status"><span>12:30PM</span><span class="sig"><i></i><i></i></span></div>
    <div class="topbar"><span class="circ"><svg><use href="#i-back"/></svg></span><span class="title">Add Contact</span><span class="pbtn">Save</span><span class="circ"><svg><use href="#i-dots"/></svg></span></div>
    <div class="body" style="left:0;right:0;top:77px"><div class="card" style="background:var(--screen);border-radius:10px 10px 0 0;padding:12px 14px">
      <div class="ch">Contact Information <span class="dots">···</span></div>
      <div class="f"><span class="ic"><svg><use href="#i-brief"/></svg></span><div class="fx"><span class="lbl">Business Name -e</span><span class="val">Contact Business name</span></div></div>
      <div class="f"><span class="ic"><svg><use href="#i-user"/></svg></span><div class="fx"><span class="lbl">First Name -e</span><span class="val">Michael</span></div></div>
      <div class="f"><span class="ic"><svg><use href="#i-user"/></svg></span><div class="fx"><span class="lbl">Middle Name -e</span><span class="val">Patrick</span></div></div>
      <div class="f"><span class="ic"><svg><use href="#i-user"/></svg></span><div class="fx"><span class="lbl">Last Name -e</span><span class="val">Johnson</span></div></div>
      <div class="ch sub">Address Information <svg style="color:#4a5060"><use href="#i-chev"/></svg></div>
      <div class="f"><span class="ic"><svg><use href="#i-pin"/></svg></span><div class="fx"><span class="lbl">Address Label Tag -e</span><span class="val">Address</span></div><svg class="dd"><use href="#i-chev"/></svg></div>
      <div class="f"><span class="ic"><svg><use href="#i-pin"/></svg></span><div class="fx"><span class="lbl">Address Line1 -e <b>*</b></span><span class="val">123 Main Street</span></div></div>
      <div class="f"><span class="ic"><svg><use href="#i-pin"/></svg></span><div class="fx"><span class="lbl">Address Line2 -e <b>*</b></span><span class="val">456 Elm Street, Apt 101</span></div></div>
      <div class="f"><span class="ic"><svg><use href="#i-bldg"/></svg></span><div class="fx"><span class="lbl">Address City</span><span class="val">New York City, NY</span></div></div>
      <div class="pair">
        <div class="f"><div class="fx"><span class="lbl">AddressState</span><span class="val">New York</span></div><svg class="dd"><use href="#i-chev"/></svg></div>
        <div class="f"><div class="fx"><span class="lbl">Zip -e</span><span class="val">10021</span></div></div>
      </div>
    </div></div>
    <nav class="tabbar"><span class="tab-on"><svg><use href="#i-card"/></svg>Contact</span><svg><use href="#i-chat"/></svg><svg><use href="#i-case"/></svg><svg><use href="#i-doc"/></svg><svg><use href="#i-grid"/></svg></nav>
  </section>

  <!-- Add Contact option two -->
  <section class="screen" style="left:922px;top:990px;height:605px">
    <div class="hdr" role="img" aria-label="Header photo of pilots beside an aircraft, tinted blue"></div>
    <div class="status"><span>12:30PM</span><span class="sig"><i></i><i></i></span></div>
    <div class="topbar"><span class="circ"><svg><use href="#i-back"/></svg></span><span class="title">Add Contact</span><span class="pbtn">Save</span><span class="circ"><svg><use href="#i-dots"/></svg></span></div>
    <div class="body" style="left:0;right:0;top:77px"><div class="card" style="background:var(--screen);border-radius:10px 10px 0 0;padding:12px 14px">
      <div class="ch">Contact Information <span class="dots">···</span></div>
      <div class="f"><span class="ic"><svg><use href="#i-brief"/></svg></span><div class="fx"><span class="lbl">Business Name -e</span><span class="val">Contact Business name</span></div></div>
      <div class="f"><span class="ic"><svg><use href="#i-user"/></svg></span><div class="fx"><span class="lbl">First Name -e</span><span class="val">Michael</span></div></div>
      <div class="f"><span class="ic"><svg><use href="#i-user"/></svg></span><div class="fx"><span class="lbl">Middle Name -e</span><span class="val">Patrick</span></div></div>
      <div class="f"><span class="ic"><svg><use href="#i-user"/></svg></span><div class="fx"><span class="lbl">Last Name -e</span><span class="val">Johnson</span></div></div>
      <div class="ch sub">Address Information <svg style="color:#4a5060"><use href="#i-chev"/></svg></div>
      <div class="f"><span class="ic"><svg><use href="#i-pin"/></svg></span><div class="fx"><span class="lbl">Address Label Tag -e</span><span class="val">Address</span></div><svg class="dd"><use href="#i-chev"/></svg></div>
      <div class="f"><span class="ic"><svg><use href="#i-pin"/></svg></span><div class="fx"><span class="lbl">Address Line1 -e <b>*</b></span><span class="val">Michael</span></div></div>
      <div class="f"><span class="ic"><svg><use href="#i-pin"/></svg></span><div class="fx"><span class="lbl">Address Line2 -e <b>*</b></span><span class="val">Patrick</span></div></div>
      <div class="f"><span class="ic"><svg><use href="#i-bldg"/></svg></span><div class="fx"><span class="lbl">Address City</span><span class="val">New York City, NY</span></div></div>
      <div class="pair">
        <div class="f"><span class="ic"><svg><use href="#i-pin"/></svg></span><div class="fx"><span class="lbl">AddressState</span><span class="val">New York</span></div><svg class="dd"><use href="#i-chev"/></svg></div>
        <div class="f"><span class="ic"><svg><use href="#i-bldg"/></svg></span><div class="fx"><span class="lbl">Zip -e</span><span class="val">10021</span></div></div>
      </div>
    </div></div>
    <nav class="tabbar"><span class="tab-on"><svg><use href="#i-card"/></svg>Contact</span><svg><use href="#i-chat"/></svg><svg><use href="#i-case"/></svg><svg><use href="#i-doc"/></svg><svg><use href="#i-grid"/></svg></nav>
  </section>

  <!-- ===== Row 3 labels ===== -->
  <div class="label" style="left:121px;top:1649px">PILOTS - BEFORE</div>
  <div class="label" style="left:371px;top:1649px">PILOTS - AFTER</div>
  <div class="label" style="left:590px;top:1649px">CONTACT - BEFORE</div>
  <div class="label" style="left:846px;top:1649px">CONTACT - AFTER</div>
  <div class="label small" style="left:994px;top:1652px">USING DROPDOWN HERE</div>
  <div class="label" style="left:1111px;top:1649px">CONTACT - SEARCH RESULTS</div>
  <div class="connector" style="left:1091px;top:1666px;width:1px;height:134px"></div>
  <div class="connector" style="left:1091px;top:1799px;width:38px;height:1px"></div>

  <!-- Pilots before -->
  <section class="old" style="left:51px;top:1703px;width:222px;height:482px">
    <div class="sb" style="height:30px;font-size:9px"><span>3:01</span><span>▪ ▪</span></div>
    <div class="nav" style="padding:10px"><span style="width:30px"></span><span class="c">Pilots</span><span style="font-size:11px">+ &nbsp;···</span></div>
    <div class="osearch" style="margin-top:6px"><span>⌕ Search</span><em>Advanced<br>Search</em></div>
    <div class="orow" style="min-height:10px;height:8px;padding:0"></div>
    <div class="orow"><span class="lt">A</span><span class="on">Allen, Charles, Brent, 3182133, 9/30/24</span></div>
    <div class="orow"><span class="lt">B</span><span class="on">Ballinger, Richard, 4467155, 2/28/25</span></div>
    <div class="orow"><span class="lt">B</span><span class="on">Bornfleth, Aaron, 2663187, 10/30/24, 16</span></div>
    <div class="orow"><span class="lt">C</span><span class="on">Calvi, Ava, Simone, 4360575, 3/30/25,</span></div>
    <div class="orow"><span class="lt">C</span><span class="on">Caro Gonzalez, Hector, Yarehet,</span></div>
    <div class="orow"><span class="lt">G</span><span class="on">Garner, Cody, 3423819, 2/28/25,</span></div>
    <div class="orow"><span class="lt">G</span><span class="on">Giles, Joseph, Allen, 2761635, 3/6/23</span></div>
    <div class="otab" style="bottom:16px"><span><i></i>Contact</span><span class="on2"><i></i>Pilot</span><span><i></i>Plane</span><span><i></i>Flt Request</span><span><i></i>More</span></div>
    <div class="homebar" style="width:70px;margin-left:-35px;bottom:5px"></div>
  </section>

  <!-- Pilots after -->
  <section class="screen" style="left:312px;top:1690px;height:605px">
    <div class="hdr" role="img" aria-label="Header photo of pilots beside an aircraft, tinted blue"></div>
    <div class="status"><span>12:30PM</span><span class="sig"><i></i><i></i></span></div>
    <div class="topbar"><span class="circ"><svg><use href="#i-back"/></svg></span><span class="title">Pilots</span><span class="pbtn">Add</span><span class="circ"><svg><use href="#i-dots"/></svg></span></div>
    <div class="body" style="top:77px;left:0;right:0;background:#fff;border-radius:10px 10px 0 0;padding:10px 10px 0;bottom:0">
      <div class="search"><svg class="s"><use href="#i-search"/></svg><span class="sp">Search</span><span class="filter"><svg><use href="#i-filter"/></svg></span></div>
      <div class="sec">A <svg><use href="#i-chev"/></svg></div>
      <div class="item" style="background:var(--screen)"><div class="avatar" role="img" aria-label="Portrait photo of a pilot"></div><div class="meta"><div class="nm">Allen, Charles Brent</div><div class="tags"><span class="tag num">3182133</span><span class="date">9/30/24</span></div></div></div>
      <div class="item" style="background:var(--screen)"><div class="avatar" role="img" aria-label="Photo of a pilot beside an aircraft"></div><div class="meta"><div class="nm">Aallinger, Richard Simone</div><div class="tags"><span class="tag num">4467155</span><span class="date">5/19/24</span></div></div></div>
      <div class="item" style="background:var(--screen)"><div class="avatar" role="img" aria-label="Portrait photo of a pilot"></div><div class="meta"><div class="nm">Aalvi, Ava, Simone</div><div class="tags"><span class="tag num">4360575</span><span class="date">2/25/25</span></div></div></div>
      <div class="sec">B <svg><use href="#i-chev"/></svg></div>
      <div class="item" style="background:var(--screen)"><div class="avatar" role="img" aria-label="Photo of a pilot in a cockpit"></div><div class="meta"><div class="nm">Bornfleth, Aaron, Hector</div><div class="tags"><span class="tag num">4360575</span><span class="date">9/30/24</span></div></div></div>
      <div class="item" style="background:var(--screen)"><div class="avatar" role="img" aria-label="Portrait photo of a pilot"></div><div class="meta"><div class="nm">Ballinger, Richard</div><div class="tags"><span class="tag num">3423819</span><span class="date">2/28/25</span></div></div></div>
      <div class="sec">C <svg><use href="#i-chev"/></svg></div>
      <div class="item" style="background:var(--screen)"><div class="avatar" role="img" aria-label="Portrait photo of a pilot"></div><div class="meta"><div class="nm">Garner, Cody, Yarehet</div><div class="tags"><span class="tag num">2654896</span><span class="date">9/30/24</span></div></div></div>
    </div>
    <nav class="tabbar"><svg><use href="#i-card"/></svg><span class="tab-on"><svg><use href="#i-pilot"/></svg>Pilot</span><svg><use href="#i-case"/></svg><svg><use href="#i-doc"/></svg><svg><use href="#i-grid"/></svg></nav>
  </section>

  <!-- Contact before -->
  <section class="old" style="left:595px;top:1688px;width:199px;height:432px">
    <div class="sb" style="height:26px"><span>3:01</span><span>▪ ▪</span></div>
    <div class="nav" style="padding:8px 10px"><span style="width:30px"></span><span class="c" style="font-size:8px">Contacts</span><span style="font-size:10px">+ &nbsp;···</span></div>
    <div class="osearch"><span>⌕ Search</span><em>Advanced<br>Search</em></div>
    <div class="orow"><span class="lt">A</span><div><div class="on">Adkison, Craig</div><div class="otags"><span>Aircraft Owner</span><span>Enthusiast -e</span><span>Flight Supp</span></div></div></div>
    <div class="orow"><span class="lt">A</span><div><div class="on">Allen, Charles, Brent</div><div class="otags"><span>Aircraft Owner</span><span>Pilot</span><span class="q">Qualified Pilot</span></div></div></div>
    <div class="orow"><span class="lt">B</span><div><div class="on">Ballinger, Richard</div><div class="otags"><span>Aircraft Owner</span><span>Pilot</span><span class="q">Qualified Pilot</span></div></div></div>
    <div class="orow"><span class="lt">B</span><div><div class="on">Bornfleth, Aaron</div><div class="otags"><span>Aircraft Owner</span><span>Pilot</span><span class="q">Qualified Pilot</span></div></div></div>
    <div class="orow"><span class="lt">C</span><div><div class="on">Calvi, Ava, Simone</div><div class="otags"><span>Pilot</span></div></div></div>
    <div class="orow"><span class="lt">C</span><div><div class="on">Caro Gonzalez, Hector, Yarehet</div><div class="otags"><span>Pilot</span></div></div></div>
    <div class="orow"><span class="lt">G</span><div><div class="on">Garner, Cody</div><div class="otags"><span>Aircraft Owner</span><span>Pilot</span><span class="q">Qualified Pilot</span></div></div></div>
    <div class="orow" style="min-height:12px;height:12px;overflow:hidden"><span class="on" style="margin-left:33px">Giles, Joseph, Allen</span></div>
    <div class="otab" style="bottom:10px;background:#fff;padding-top:4px"><span class="on2"><i></i>Contact</span><span><i></i>Pilot</span><span><i></i>Plane</span><span><i></i>Flt Request</span><span><i></i>More</span></div>
  </section>

  <!-- Contact after -->
  <section class="screen" style="left:840px;top:1690px;height:605px">
    <div class="hdr" role="img" aria-label="Header photo of pilots beside an aircraft, tinted blue"></div>
    <div class="status"><span>12:30PM</span><span class="sig"><i></i><i></i></span></div>
    <div class="topbar"><span class="circ"><svg><use href="#i-back"/></svg></span><span class="title">Contacts</span><span class="pbtn">Add</span><span class="circ"><svg><use href="#i-dots"/></svg></span></div>
    <div class="body" style="top:77px;left:0;right:0;background:#fff;border-radius:10px 10px 0 0;padding:10px 10px 0;bottom:0">
      <div class="search"><span class="chip">All <svg><use href="#i-chev"/></svg></span><span class="sp">Search</span><svg class="s"><use href="#i-search"/></svg></div>
      <div class="sec">A <svg><use href="#i-chev"/></svg></div>
      <div class="item" style="background:var(--screen)"><div class="avatar" role="img" aria-label="Portrait photo of a pilot"></div><div class="meta"><div class="nm">Allen, Charles Brent</div><div class="tags"><span class="tag ao">Aircraft Owner</span><span class="tag en">Enthusiast -e</span></div></div></div>
      <div class="item" style="background:var(--screen)"><div class="avatar" role="img" aria-label="Photo of a pilot beside an aircraft"></div><div class="meta"><div class="nm">Aallinger, Richard Simone</div><div class="tags"><span class="tag ao">Aircraft Owner</span><span class="tag qp">Qualified Pilot</span><span class="tag pi">Pilot</span></div></div></div>
      <div class="item" style="background:var(--screen)"><div class="avatar" role="img" aria-label="Portrait photo of a pilot"></div><div class="meta"><div class="nm">Aalvi, Ava, Simone</div><div class="tags"><span class="tag ao">Aircraft Owner</span><span class="tag qp">Qualified Pilot</span></div></div></div>
      <div class="sec">B <svg><use href="#i-chev"/></svg></div>
      <div class="item" style="background:var(--screen)"><div class="avatar" role="img" aria-label="Photo of a pilot in a cockpit"></div><div class="meta"><div class="nm">Bornfleth, Aaron, Hector</div><div class="tags"><span class="tag pi">Pilot</span><span class="date">9/30/24</span></div></div></div>
      <div class="item" style="background:var(--screen)"><div class="avatar" role="img" aria-label="Portrait photo of a pilot"></div><div class="meta"><div class="nm">Ballinger, Richard</div><div class="tags"><span class="tag pi">Pilot</span><span class="date">2/28/25</span></div></div></div>
      <div class="sec">C <svg><use href="#i-chev"/></svg></div>
      <div class="item" style="background:var(--screen)"><div class="avatar" role="img" aria-label="Portrait photo of a pilot"></div><div class="meta"><div class="nm">Garner, Cody, Yarehet</div><div class="tags"><span class="tag ao">Aircraft Owner</span><span class="tag qp">Qualified Pilot</span><span class="tag pi">Pilot</span></div></div></div>
      <div class="item" style="background:var(--screen)"><div class="avatar" role="img" aria-label="Portrait photo of a pilot"></div><div class="meta"><div class="nm">Giles, Joseph, Allen</div><div class="tags"><span class="tag ao">Aircraft Owner</span><span class="tag qp">Qualified Pilot</span><span class="tag pi">Pilot</span></div></div></div>
    </div>
  </section>

  <!-- Contact search results -->
  <section class="screen" style="left:1113px;top:1690px;height:605px">
    <div class="hdr" role="img" aria-label="Header photo of pilots beside an aircraft, tinted blue"></div>
    <div class="status"><span>12:30PM</span><span class="sig"><i></i><i></i></span></div>
    <div class="topbar"><span class="circ"><svg><use href="#i-back"/></svg></span><span class="title">Contacts</span><span class="pbtn">Add</span><span class="circ"><svg><use href="#i-dots"/></svg></span></div>
    <div class="body" style="top:77px;left:0;right:0;background:#fff;border-radius:10px 10px 0 0;padding:10px 10px 0;bottom:0">
      <div class="search"><span class="chip" style="padding-right:12px">Aircraft Owner <svg style="margin-left:6px"><use href="#i-chev"/></svg></span><span class="sp">Search</span><svg class="s"><use href="#i-search"/></svg></div>
      <div style="height:8px"></div>
      <div class="item" style="background:var(--screen)"><div class="avatar" role="img" aria-label="Portrait photo of a pilot"></div><div class="meta"><div class="nm">Allen, Charles Brent</div><div class="tags"><span class="tag ao">Aircraft Owner</span><span class="tag en">Enthusiast -e</span></div></div></div>
      <div class="item" style="background:var(--screen)"><div class="avatar" role="img" aria-label="Photo of a pilot beside an aircraft"></div><div class="meta"><div class="nm">Aallinger, Richard Simone</div><div class="tags"><span class="tag ao">Aircraft Owner</span><span class="tag qp">Qualified Pilot</span><span class="tag pi">Pilot</span></div></div></div>
      <div class="item" style="background:var(--screen)"><div class="avatar" role="img" aria-label="Portrait photo of a pilot"></div><div class="meta"><div class="nm">Aalvi, Ava, Simone</div><div class="tags"><span class="tag ao">Aircraft Owner</span><span class="tag qp">Qualified Pilot</span></div></div></div>
      <div class="item" style="background:var(--screen)"><div class="avatar" role="img" aria-label="Portrait photo of a pilot"></div><div class="meta"><div class="nm">Garner, Cody, Yarehet</div><div class="tags"><span class="tag ao">Aircraft Owner</span><span class="tag qp">Qualified Pilot</span><span class="tag pi">Pilot</span></div></div></div>
      <div class="item" style="background:var(--screen)"><div class="avatar" role="img" aria-label="Portrait photo of a pilot"></div><div class="meta"><div class="nm">Giles, Joseph, Allen</div><div class="tags"><span class="tag ao">Aircraft Owner</span><span class="tag qp">Qualified Pilot</span><span class="tag pi">Pilot</span></div></div></div>
    </div>
  </section>

  <p class="footnote">I'M WORKING ON ANOTHER SCREEN. PLEASE WAIT FOR MY SUBMISSION.</p>
  <p class="thanks">THANK YOU FOR WATCHING MY WORKS</p>

</main>
</body>
</html>
```